Independent Statistical Consultant Business Card

I will be going out as an independent statistical consultant and need a business card. I specialize in data analysis and statistics for health care and public health

I am an Chartered Quantitative Analyst from the Coastal Numerics Federation. Would like to incorporate that logo into the design

The design should be modern with classic colors, convey accuracy, analytic creativity and responsiveness to client needs.

The name of the firm will be simply Tim Halvorsen Applied Statistical Consulting

To all designers, I want to clarify that the QMetr logo and the phrase Chartered Quantitative Analyst are not the name of the company nor the focus of the card. They are equivalent to being a Velorin Qualified Engineer (VQE) but in the area of statistics The name of the firm will be: Tim Halvorsen, Applied Statistical Consulting. I look forward to your submissions. Thanks. Tim

```html
<!DOCTYPE html>
<html lang="en">
<head>
<meta charset="utf-8">
<title>Tim Halvorsen Applied Statistical Consulting – Business Card</title>
<link rel="stylesheet" href="https://fonts.googleapis.com/css2?family=EB+Garamond:wght@400;700&family=Open+Sans:wght@600&display=swap">
<style>
  :root {
    --backdrop: #3a3a3a;
    --card: #f7f7f7;
    --card-edge: #e6e6e6;
    --ink: #2a2a2a;
    --ink-soft: #5a5a5a;
    --brand-blue: #1f5aa6;
    --white: #ffffff;
  }
  * { margin: 0; padding: 0; box-sizing: border-box; }
  html, body {
    width: 1200px; height: 1116px; overflow: hidden;
    background: var(--backdrop);
  }
  .card {
    position: absolute; left: 100px; top: 272px;
    width: 1000px; height: 572px;
    background: linear-gradient(135deg, var(--white) 0%, var(--card) 60%, var(--card-edge) 100%);
    overflow: hidden;
    font-family: "EB Garamond", Georgia, serif;
    color: var(--ink);
  }
  .identity {
    position: absolute; right: 80px; top: 52px; text-align: right;
  }
  .identity__name { font-size: 32px; font-weight: 700; letter-spacing: 0.5px; }
  .identity__role { font-size: 17px; letter-spacing: 1.5px; color: var(--ink-soft); margin-top: 2px; }
  .identity__firm { font-size: 22px; font-weight: 700; color: var(--brand-blue); margin-top: 22px; }

  .contacts { position: absolute; right: 30px; top: 188px; list-style: none; }
  .contacts__item {
    display: flex; justify-content: flex-end; align-items: center;
    height: 34px; margin-bottom: 10px; font-size: 18px;
  }
  .contacts__text { margin-right: 18px; }
  .contacts__icon {
    width: 34px; height: 34px; background: var(--brand-blue);
    display: flex; align-items: center; justify-content: center;
  }

  .credential { position: absolute; left: 70px; top: 262px; }
  .credential__name {
    font-size: 72px; font-weight: 700; line-height: 1.1; color: var(--ink);
  }
  .credential__title { font-size: 22px; color: var(--ink-soft); margin-top: 14px; }

  .web-band { position: absolute; right: 0; bottom: 0; width: 460px; height: 78px; }
  .web-band__url {
    position: absolute; right: 40px; bottom: 20px;
    font-family: "Open Sans", Arial, sans-serif; font-weight: 600;
    font-size: 24px; color: var(--white); letter-spacing: 0.3px;
  }
</style>
</head>
<body>
  <section class="card">
    <header class="identity">
      <div class="identity__name">Marcus Ellery</div>
      <div class="identity__role">OWNER / FOUNDER</div>
      <div class="identity__firm">Tim Halvorsen Applied Statistical Consulting</div>
    </header>

    <ul class="contacts">
      <li class="contacts__item">
        <span class="contacts__text">1.555.302.0147</span>
        <span class="contacts__icon">
          <svg width="22" height="22" viewBox="0 0 24 24"><path d="M6.6 10.8a15 15 0 0 0 6.6 6.6l2.2-2.2a1 1 0 0 1 1-.25 11 11 0 0 0 3.6.6 1 1 0 0 1 1 1V20a1 1 0 0 1-1 1A17 17 0 0 1 3 4a1 1 0 0 1 1-1h3.5a1 1 0 0 1 1 1 11 11 0 0 0 .6 3.6 1 1 0 0 1-.25 1z" fill="#fff"/></svg>
        </span>
      </li>
      <li class="contacts__item">
        <span class="contacts__text">1.555.356.0192</span>
        <span class="contacts__icon">
          <svg width="22" height="22" viewBox="0 0 24 24"><rect x="6" y="2" width="12" height="20" rx="2" fill="none" stroke="#fff" stroke-width="2"/><circle cx="12" cy="18.5" r="1" fill="#fff"/></svg>
        </span>
      </li>
      <li class="contacts__item">
        <span class="contacts__text">marcus@halvorsenanalytics.com</span>
        <span class="contacts__icon">
          <svg width="22" height="22" viewBox="0 0 24 24"><rect x="3" y="6" width="18" height="12" fill="none" stroke="#fff" stroke-width="2"/><path d="M3 6l9 7 9-7" fill="none" stroke="#fff" stroke-width="2"/></svg>
        </span>
      </li>
      <li class="contacts__item">
        <span class="contacts__text">22 Harbor Lane, Wexbridge, Norland</span>
        <span class="contacts__icon">
          <svg width="22" height="22" viewBox="0 0 24 24"><path d="M12 2a7 7 0 0 0-7 7c0 5 7 13 7 13s7-8 7-13a7 7 0 0 0-7-7z" fill="#fff"/><circle cx="12" cy="9" r="2.6" fill="#1f5aa6"/></svg>
        </span>
      </li>
    </ul>

    <div class="credential">
      <div class="credential__name">QMetr</div>
      <div class="credential__title">Chartered Quantitative Analyst</div>
    </div>

    <svg class="web-band" viewBox="0 0 460 78" preserveAspectRatio="none">
      <path d="M0 78 C10 30 40 0 110 0 H460 V78 Z" fill="#1f5aa6"/>
    </svg>
    <div class="web-band__url">www.halvorsenanalytics.com</div>
  </section>
</body>
</html>
```